Home Staging Company needs business card design

We're a home staging company called Brightly Settled Home Staging. We would like a business card design that includes aqua and gray. Our current logo of house within chair is fine but I find we almost always use the logo in one color. I'll upload images of front and back of our current card and our logo. Note that we have dropped "Solutions" from our company name and don't want to include it on the card.

Target Market(s)

Realtors and homeowners - people interested in selling their homes

Contact Information for Business Card

Marisol Thistlewood
Brightly Settled Home Staging
757-555-0193
www.brightlysettled.com
marisol@brightlysettled.com

Font styles to use
Serif
Script

Requirements
Must have
• My logo and contact details
• UPDATE***
• I forgot to say that the company name should be included on the front of the card somehow.

```html
<!DOCTYPE html>
<html lang="en">
<head>
<meta charset="utf-8">
<title>Brightly Settled Home Staging – Business Card</title>
<link rel="stylesheet" href="https://fonts.googleapis.com/css2?family=Roboto:wght@400;500&family=Questrial&display=swap">
<style>
  :root {
    --backdrop: #e4dfd9;
    --card-top: #f5f6f5;
    --card-bottom: #e9ecea;
    --aqua: #4fb1bd;
    --aqua-deep: #3b9aa6;
    --charcoal: #3a3a3c;
    --gray: #4a4a4c;
  }
  html, body {
    margin: 0;
    padding: 0;
    width: 1200px;
    height: 1054px;
    overflow: hidden;
    background: var(--backdrop);
  }
  .business-card {
    position: absolute;
    left: 100px;
    top: 227px;
    width: 1000px;
    height: 600px;
    border-radius: 26px;
    background: linear-gradient(160deg, var(--card-top), var(--card-bottom));
    box-shadow: 0 18px 40px rgba(0,0,0,0.12);
    overflow: hidden;
  }
  .card-edge {
    position: absolute;
    left: 0;
    right: 0;
    bottom: 0;
    height: 9px;
    background: var(--aqua);
  }
  .brand {
    position: absolute;
    left: 60px;
    width: 400px;
    top: 140px;
    text-align: center;
  }
  .brand-dot {
    display: block;
    width: 120px;
    height: 120px;
    margin: 0 auto 34px;
    border-radius: 50%;
    background: var(--aqua);
  }
  .brand-name,
  .brand-tagline {
    display: block;
    font-family: "Roboto", sans-serif;
    font-weight: 500;
    color: var(--aqua-deep);
  }
  .brand-name {
    font-size: 42px;
    line-height: 1.1;
  }
  .brand-tagline {
    font-size: 19px;
    letter-spacing: 0.42em;
    margin-top: 8px;
  }
  .contact-block {
    position: absolute;
    left: 535px;
    top: 190px;
  }
  .person-name {
    margin: 0;
    font-family: "Roboto", sans-serif;
    font-weight: 400;
    font-size: 36px;
    color: var(--charcoal);
  }
  .person-name .surname { color: var(--aqua); }
  .person-title {
    margin: 10px 0 0;
    font-family: "Questrial", sans-serif;
    font-size: 22px;
    color: var(--gray);
  }
  .contact-list {
    list-style: none;
    margin: 32px 0 0;
    padding: 0;
  }
  .contact-list li {
    display: flex;
    align-items: center;
    height: 37px;
    font-family: "Questrial", sans-serif;
    font-size: 24px;
    color: var(--charcoal);
  }
  .contact-icon {
    width: 22px;
    height: 22px;
    margin-right: 25px;
    flex: none;
  }
  .contact-icon * { fill: var(--aqua); }
</style>
</head>
<body>
  <div class="business-card">
    <div class="brand">
      <span class="brand-dot"></span>
      <span class="brand-name">Brightly Settled</span>
      <span class="brand-tagline">HOME STAGING</span>
    </div>

    <div class="contact-block">
      <h1 class="person-name">Marisol <span class="surname">Thistlewood</span></h1>
      <p class="person-title">Managing Director</p>
      <ul class="contact-list">
        <li>
          <svg class="contact-icon" viewBox="0 0 24 24" aria-hidden="true">
            <path d="M3 8c0-2 2-4 9-4s9 2 9 4v2h-5V8H8v2H3z"/>
            <path d="M6 12h12l2 8H4z"/>
          </svg>
          757-555-0193
        </li>
        <li>
          <svg class="contact-icon" viewBox="0 0 24 24" aria-hidden="true">
            <path fill-rule="evenodd" d="M12 2a10 10 0 1 1 0 20a10 10 0 0 1 0-20zm-1 2.1A8 8 0 0 0 4.1 11H8c.1-2.6.9-5 3-6.9zm2 0c2.1 1.9 2.9 4.3 3 6.9h3.9A8 8 0 0 0 13 4.1zM10 11h4c-.1-2.2-.8-4.2-2-5.6-1.2 1.4-1.9 3.4-2 5.6zm0 2c.1 2.2.8 4.2 2 5.6 1.2-1.4 1.9-3.4 2-5.6zm-5.9 0A8 8 0 0 0 11 19.9C8.9 18 8.1 15.6 8 13zm11.9 0c-.1 2.6-.9 5-3 6.9a8 8 0 0 0 6.9-6.9z"/>
          </svg>
          www.brightlysettled.com
        </li>
        <li>
          <svg class="contact-icon" viewBox="0 0 24 24" aria-hidden="true">
            <path d="M2 5h20v14H2zm2 2v.5l8 5.5 8-5.5V7l-8 5.2z" fill-rule="evenodd"/>
          </svg>
          marisol@brightlysettled.com
        </li>
      </ul>
    </div>

    <div class="card-edge"></div>
  </div>
</body>
</html>
```